ByteLotus.com Redesign

Please read the notes and see the site-map attached.
Updates

We are looking for something highly creative. Please provide your best work. Best of luck and thank you very much for your hard work!

Project Deadline Extended
Reason: I am seeing good designs but I am not seeing great designs. I really need a design that is unique and is going to wow me. No one is required to stick to the existing color schemes etc. You are free to use other colors etc. I am seeing a lot of the same colors that are used on the site now.

Target Market(s)

Business and entrepreneurs mainly. People looking to build applications, software or launch web or mobile tech products.

Colors

Designer to choose colors to be used in the design.

Requirements
Must have
• See my attached html file.
Nice to have
Should not have
• No sure

```html
<!DOCTYPE html>
<html lang="en">
<head>
<meta charset="utf-8">
<title>ByteLotus.com</title>
<link href="https://fonts.googleapis.com/css2?family=Open+Sans:wght@400;600;700;800&display=swap" rel="stylesheet">
<style>
:root{
  --green:#6cbb3c;
  --green-dark:#58a02c;
  --navy:#1d3f5e;
  --navy-deep:#16324b;
  --teal-band:#1f4660;
  --footer:#1c2530;
  --footer-base:#141b23;
  --ink:#2a2f36;
  --muted:#8a9099;
  --line:#dde1e5;
  --paper:#ffffff;
  --soft:#f1f3f5;
}
*{box-sizing:border-box;margin:0;padding:0}
html,body{width:764px;height:1200px;overflow:hidden}
body{font-family:"Open Sans",Arial,sans-serif;color:var(--ink);background:var(--paper);font-size:10px}
.site{width:764px;height:1200px;position:relative}

/* header */
.masthead{height:66px;display:flex;align-items:center;justify-content:space-between;padding:0 40px 0 44px;position:relative}
.brand{display:flex;align-items:center;gap:8px;font-weight:700;font-size:18px;color:var(--navy)}
.brand-mark{width:22px;height:22px;border-radius:50%;background:var(--green)}
.contact-line{position:absolute;top:8px;right:42px;font-size:7px;color:var(--muted)}
.nav{display:flex;gap:4px;margin-top:14px}
.nav a{font-size:9px;color:var(--ink);text-decoration:none;padding:6px 9px}
.nav a.active{background:var(--green);color:#fff}

/* hero */
.hero{height:241px;position:relative;color:#fff;overflow:hidden}
.hero-photo{position:absolute;inset:0;background:linear-gradient(135deg,#cfd3d6 0%,#9aa1a7 35%,#5a6169 70%,#2e343a 100%)}
.hero-shade{position:absolute;left:0;right:0;bottom:0;height:150px;background:linear-gradient(180deg,rgba(20,30,40,0) 0%,rgba(20,30,40,.75) 60%)}
.hero-copy{position:absolute;left:0;right:0;top:100px;text-align:center}
.hero-copy h1{font-size:25px;font-weight:800;letter-spacing:.5px}
.hero-copy p{width:330px;margin:8px auto 0;font-size:8px;line-height:1.5;opacity:.9}
.hero-actions{display:flex;justify-content:center;gap:10px;margin-top:10px}
.btn-outline{border:1px solid #fff;font-size:8px;padding:6px 16px;font-weight:600}
.hire-badge{position:absolute;right:38px;top:96px;background:#fff;color:var(--navy);font-size:8px;font-weight:700;padding:8px 10px;line-height:1.3}
.hire-badge span{display:block;color:var(--muted);font-weight:400;font-size:6px}

/* services */
.services{height:205px;position:relative}
.services-art{position:absolute;left:60px;top:22px;width:110px;height:165px;background:linear-gradient(180deg,#e4eaef,#c9d3dc);border-radius:4px}
.service-grid{position:absolute;left:300px;top:14px;width:350px;display:grid;grid-template-columns:1fr 1fr;row-gap:12px}
.service{display:flex;align-items:center;gap:14px;height:80px;padding-left:16px;border-bottom:1px solid var(--line)}
.service:nth-child(odd){border-right:1px solid var(--line)}
.service:nth-child(n+3){border-bottom:none}
.service-icon{width:52px;height:52px;border-radius:50%;background:#2c3a4a;flex:none;display:flex;align-items:center;justify-content:center}
.service-name{font-size:8px;color:var(--muted);line-height:1.3}
.service.featured .service-name{color:var(--green-dark);font-weight:700;font-size:10px}

/* proof */
.proof{height:268px;display:flex}
.cases{width:382px;background:var(--navy);color:#fff;padding:20px 22px 0 48px;position:relative}
.loves{width:382px;background:var(--green);color:#fff;padding:20px 44px 0 22px;position:relative}
.proof h2{font-size:12px;font-weight:700;letter-spacing:.5px;display:flex;align-items:center;gap:8px}
.proof h2 i{display:inline-block;width:18px;height:14px;background:#fff;opacity:.85}
.case-card{margin-top:12px;background:var(--navy-deep);padding:8px 12px;position:relative}
.case-card + .case-card{margin-top:6px}
.case-card b{font-size:10px;display:block}
.case-card p{font-size:7px;opacity:.8;line-height:1.45;margin-top:2px}
.case-zoom{position:absolute;right:12px;top:9px;width:26px;height:26px;border:1px solid #fff;border-radius:50%}
.proof .more{position:absolute;bottom:14px;font-size:8px;font-weight:700}
.quote-block{margin-top:14px;font-size:7px;line-height:1.5}
.quote-block + .quote-block{margin-top:12px}
.quote-block cite{display:block;font-style:normal;font-weight:700;margin-top:4px}

/* quote form */
.quote{height:167px;background:var(--soft);text-align:center;padding-top:20px}
.quote-icon{width:22px;height:22px;border-radius:50%;background:var(--navy);margin:0 auto}
.quote h2{font-size:12px;font-weight:700;color:var(--navy);margin-top:4px}
.quote-rule{width:60px;height:2px;background:var(--green);margin:6px auto 0}
.quote-form{display:flex;justify-content:center;gap:8px;margin-top:16px}
.field-col{display:flex;flex-direction:column;gap:8px}
.field{background:#fff;border:1px solid var(--line);width:150px;height:24px;font-size:7px;color:var(--muted);text-align:left;padding:7px 8px}
.field.tall{width:170px;height:56px}
.send{width:150px;height:56px;background:var(--green);color:#fff;font-weight:700;font-size:12px;display:flex;flex-direction:column;justify-content:center}
.send span{font-size:6px;font-weight:400;margin-top:2px}

/* social band */
.follow{height:89px;background:var(--teal-band);display:flex;align-items:center;justify-content:center;gap:8px;color:#fff}
.follow strong{font-size:12px;margin-right:6px}
.chip{width:24px;height:24px}

/* footer */
.footer{height:142px;background:var(--footer);color:#c5ccd3;display:flex;padding:20px 44px 0 122px;gap:60px}
.footer-links{list-style:none;font-size:8px;line-height:1.75}
.footer-links li::before{content:"› ";color:var(--green)}
.footer-address{font-size:7px;line-height:1.6;width:120px}
.footer-address b{color:#fff;font-size:8px;display:block;margin-bottom:3px}
.footer-brand{margin-left:auto;font-size:7px;line-height:1.6}
.footer-brand .brand{color:var(--green);font-size:15px;margin-bottom:6px}
.base-bar{height:22px;background:var(--footer-base)}
</style>
</head>
<body>
<div class="site">

  <header class="masthead">
    <div class="brand"><span class="brand-mark"></span>ByteLotus</div>
    <div class="contact-line">+1 (555) 014-2210 &nbsp;|&nbsp; hello@bytelotus.example</div>
    <nav class="nav">
      <a class="active">Home</a><a>Who We Are</a><a>What We Do</a><a>Case Studies</a><a>Blog</a><a>Reach Us</a>
    </nav>
  </header>

  <section class="hero">
    <div class="hero-photo" role="img" aria-label="Photo of a team working at a desk with laptops and papers"></div>
    <div class="hero-shade"></div>
    <div class="hero-copy">
      <h1>YOUR DEVELOPMENT PARTNER</h1>
      <p>We design and build websites, apps and custom software that help ambitious businesses launch faster and grow with confidence, from idea to production.</p>
      <div class="hero-actions"><span class="btn-outline">OUR SERVICES</span><span class="btn-outline">GET A QUOTE</span></div>
    </div>
    <div class="hire-badge">HIRE US NOW<span>Start your project</span></div>
  </section>

  <section class="services">
    <div class="services-art" role="img" aria-label="Illustration of a calm figure seated beside a laptop"></div>
    <div class="service-grid">
      <div class="service"><div class="service-icon"><svg width="26" height="20"><rect x="1" y="1" width="24" height="15" fill="none" stroke="#fff" stroke-width="2"/><rect x="8" y="17" width="10" height="2" fill="#fff"/></svg></div><div class="service-name">Web<br>Development</div></div>
      <div class="service featured"><div class="service-icon"><svg width="24" height="24"><circle cx="12" cy="12" r="8" fill="none" stroke="#6cbb3c" stroke-width="3"/><circle cx="12" cy="12" r="3" fill="#6cbb3c"/></svg></div><div class="service-name">Custom Software<br>Development</div></div>
      <div class="service"><div class="service-icon"><svg width="24" height="24"><circle cx="12" cy="8" r="5" fill="#fff"/><rect x="4" y="15" width="16" height="7" rx="3" fill="#fff"/></svg></div><div class="service-name">User Experience<br>Design</div></div>
      <div class="service"><div class="service-icon"><svg width="16" height="26"><rect x="1" y="1" width="14" height="24" rx="2" fill="none" stroke="#fff" stroke-width="2"/><circle cx="8" cy="21" r="1.5" fill="#fff"/></svg></div><div class="service-name">Mobile App<br>Development</div></div>
    </div>
  </section>

  <section class="proof">
    <div class="cases">
      <h2><i></i>CASE STUDIES</h2>
      <div class="case-card"><b>Client:</b><p>Clearpoint Labs<br>User Experience Design, Product Development</p><span class="case-zoom"></span></div>
      <div class="case-card"><b>Client:</b><p>Maple Course Co.<br>Planning, Web Platform, User Experience Design, Product Development</p></div>
      <div class="case-card"><b>Client:</b><p>Harbor Lane Media Group<br>Web Development, Custom CMS, API Integration, Hosting</p></div>
      <span class="more">VIEW ALL CASES &gt;&gt;</span>
    </div>
    <div class="loves">
      <h2><i></i>WHY CLIENTS LOVE US!</h2>
      <div class="quote-block">“Working with this team has been a pleasure from day one. They understood our goals quickly, shipped on time and kept us informed at every step. Our new platform is faster, cleaner and easier for our customers to use.”<cite>Dana Reyes, Managing Director, Northfield Capital</cite></div>
      <div class="quote-block">“They took a rough idea and turned it into a polished product. The process was clear, communication was excellent and the results exceeded our expectations.”<cite>Marc Olsen, CEO, Brightpath Ventures</cite></div>
      <span class="more">VIEW ALL &gt;&gt;</span>
    </div>
  </section>

  <section class="quote">
    <div class="quote-icon"></div>
    <h2>GET A QUOTE</h2>
    <div class="quote-rule"></div>
    <div class="quote-form">
      <div class="field-col"><div class="field">Name</div><div class="field">E-mail</div></div>
      <div class="field tall">Message</div>
      <div class="send">SEND &gt;&gt;<span>Get a Quote Now</span></div>
    </div>
  </section>

  <section class="follow">
    <strong>Follow us :</strong>
    <span class="chip" style="background:#d84a38"></span>
    <span class="chip" style="background:#3b5998"></span>
    <span class="chip" style="background:#f57d00"></span>
    <span class="chip" style="background:#0077b5"></span>
    <span class="chip" style="background:#29a9e1"></span>
    <span class="chip" style="background:#3aa3d6"></span>
  </section>

  <footer class="footer">
    <ul class="footer-links">
      <li>Home</li><li>Who We Are</li><li>What We Do</li><li>Case Studies</li><li>Blog</li><li>Reach Us</li><li>Privacy Policy</li>
    </ul>
    <div class="footer-address"><b>ByteLotus LLC</b>120 Harbor Street, Suite 4<br>Lakeview, FL 30000<br>Phone: +1 (555) 014-2210<br>hello@bytelotus.example</div>
    <div class="footer-brand"><div class="brand">ByteLotus</div>Copyright © 2016 ByteLotus LLC<br>All Rights Reserved.</div>
  </footer>
  <div class="base-bar"></div>

</div>
</body>
</html>
```